Business card design for my company.
I would like the card's background colour to be black. You can also see our web site to get an idea of our brand. https://www.tmwhomecrafting.com.au/
- Name
- Email

```html
<!DOCTYPE html>
<html lang="en">
<head>
<meta charset="utf-8">
<title>TMW Home Crafting – Business Card</title>
<link href="https://fonts.googleapis.com/css2?family=Montserrat:wght@400;500;700;800&display=swap" rel="stylesheet">
<style>
  :root {
    --backdrop: #2a2a2c;
    --card-black: #151515;
    --brand-green: #0a9447;
    --text-light: #f2f2f2;
    --text-muted: #d6d6d6;
  }
  * { box-sizing: border-box; margin: 0; padding: 0; }
  html, body {
    width: 1200px; height: 900px; overflow: hidden;
    background: var(--backdrop);
    font-family: "Montserrat", sans-serif;
  }
  .canvas {
    position: relative; width: 1200px; height: 900px;
    display: flex; flex-direction: column; align-items: center; justify-content: center; gap: 56px;
  }
  .card {
    width: 560px; height: 320px; border-radius: 22px;
    position: relative; overflow: hidden;
  }
  .card-back { background: var(--card-black); display: flex; align-items: center; }
  .card-front { background: var(--brand-green); display: flex; align-items: center; justify-content: center; }

  .wordmark {
    display: flex; align-items: center; gap: 12px;
    font-weight: 800; letter-spacing: 0.04em; line-height: 1.05;
    text-transform: uppercase;
  }
  .wordmark-square { width: 18px; height: 18px; flex: none; }
  .card-back .wordmark { color: var(--text-light); font-size: 26px; }
  .card-back .wordmark-square { background: var(--brand-green); }
  .card-front .wordmark { color: #fff; font-size: 44px; gap: 18px; }
  .card-front .wordmark-square { width: 28px; height: 28px; background: #fff; }

  .brand-panel { width: 250px; padding-left: 36px; }
  .divider { width: 2px; height: 190px; background: var(--brand-green); }
  .details { padding-left: 26px; color: var(--text-light); }
  .person-name { color: var(--brand-green); font-weight: 700; font-size: 27px; line-height: 1.1; }
  .person-role { font-size: 14px; color: var(--text-muted); margin-top: 4px; }
  .location { font-size: 14px; color: var(--text-muted); margin: 18px 0 14px; }
  .contact-list { list-style: none; display: flex; flex-direction: column; gap: 8px; }
  .contact-item { display: flex; align-items: center; gap: 9px; font-size: 14px; color: var(--text-light); }
  .contact-icon { width: 14px; height: 14px; flex: none; fill: var(--brand-green); }
</style>
</head>
<body>
<main class="canvas">
  <section class="card card-back" aria-label="Business card back">
    <div class="brand-panel">
      <div class="wordmark"><span class="wordmark-square"></span><span>TMW Home<br>Crafting</span></div>
    </div>
    <div class="divider"></div>
    <div class="details">
      <h1 class="person-name">Liam Harcourt</h1>
      <p class="person-role">General Manager</p>
      <p class="location">Devonport, Tasmania, Australia</p>
      <ul class="contact-list">
        <li class="contact-item">
          <svg class="contact-icon" viewBox="0 0 16 16" aria-hidden="true"><path d="M3.6 1.5l2.3 2.6-1.3 1.7c.9 1.9 2.4 3.4 4.3 4.3l1.7-1.3 2.6 2.3-1.3 2.4C7.2 13.3 2.7 8.8 2.5 2.8z"/></svg>
          <span>0400 123 456</span>
        </li>
        <li class="contact-item">
          <svg class="contact-icon" viewBox="0 0 16 16" aria-hidden="true"><path d="M1 3.5h14v9H1z M1.5 4l6.5 5 6.5-5" fill="none" stroke="#0a9447" stroke-width="1.6"/></svg>
          <span>info@tmwhomecrafting.com.au</span>
        </li>
        <li class="contact-item">
          <svg class="contact-icon" viewBox="0 0 16 16" aria-hidden="true"><circle cx="8" cy="8" r="6.5" fill="none" stroke="#0a9447" stroke-width="1.6"/><path d="M1.5 8h13M8 1.5c-3 3.5-3 9.5 0 13M8 1.5c3 3.5 3 9.5 0 13" fill="none" stroke="#0a9447" stroke-width="1.2"/></svg>
          <span>www.tmwhomecrafting.com.au</span>
        </li>
      </ul>
    </div>
  </section>

  <section class="card card-front" aria-label="Business card front">
    <div class="wordmark"><span class="wordmark-square"></span><span>TMW Home<br>Crafting</span></div>
  </section>
</main>
</body>
</html>
```